Business Card for beauty technology startup

Design Glimora Business Card for a Beauty, based on the website identity and colors (https://www.glimora-example.com).
Glimora is a beauty tech startup that gathers helpful product info for beauty lovers and consumers (such as availability on stores, price range and product reviews) for makeup products. The card design must be young, colorful but clean, and very modern.

Target Market(s)

woman, 15-35

Industry/Entity Type

Cosmetics

Contact Information for Business Card

Full Name, address, phone

Font styles to use
Other font styles liked:
• Advent Pro

Colors
e34297
86cfc6
ffffff
5c5c5c
e8e8e8
e667a6
b2b2b2

Requirements
Must have
• One full colored side with a creative design and another with card info
• Use Color palette: #95C5C5 and/or #D38AA5
• Use fonts: Advent Pro
• Use website identity: https://www.glimora-example.com
Nice to have
• If needed extra font: Roboto

```html
<!DOCTYPE html>
<html lang="en">
<head>
<meta charset="utf-8">
<title>Glimora Business Card</title>
<link rel="stylesheet" href="https://fonts.googleapis.com/css2?family=Advent+Pro:wght@300;400&family=Roboto:wght@400;500&display=swap">
<style>
  :root {
    --rose: #be8398;
    --plum: #4a3340;
    --ink: #4a3f46;
    --paper: #ffffff;
    --backdrop: #e8e8e8;
  }
  * { margin: 0; padding: 0; box-sizing: border-box; }
  html, body {
    width: 1200px;
    height: 1155px;
    overflow: hidden;
    background: var(--backdrop);
  }
  .card {
    position: absolute;
    left: 219px;
    width: 757px;
    height: 434px;
    border-radius: 32px;
    overflow: hidden;
  }
  .card--front {
    top: 134px;
    background: var(--rose);
  }
  .card--back {
    top: 596px;
    background: var(--paper);
  }
  .card__art {
    position: absolute;
    inset: 0;
    width: 100%;
    height: 100%;
  }
  .wordmark {
    position: absolute;
    font-family: "Advent Pro", sans-serif;
    font-weight: 300;
    font-size: 74px;
    line-height: 1;
    letter-spacing: 10px;
  }
  .card--front .wordmark {
    left: 0;
    right: 0;
    top: 272px;
    text-align: center;
    color: var(--paper);
    padding-left: 10px;
  }
  .card--back .wordmark {
    right: 28px;
    top: 336px;
    color: var(--plum);
    letter-spacing: 6px;
    font-size: 70px;
  }
  .contact {
    position: absolute;
    left: 38px;
    top: 192px;
    font-family: "Roboto", sans-serif;
    color: var(--ink);
  }
  .contact__name {
    font-weight: 500;
    font-size: 24px;
    color: var(--rose);
    letter-spacing: 0.3px;
  }
  .contact__role {
    font-size: 15px;
    letter-spacing: 0.8px;
    margin-top: 4px;
  }
  .contact__address {
    font-size: 20px;
    line-height: 28px;
    margin-top: 12px;
  }
  .contact__list {
    list-style: none;
    margin-top: 8px;
    font-size: 20px;
    line-height: 27.5px;
  }
  .contact__list li {
    display: flex;
    align-items: center;
  }
  .contact__icon {
    width: 14px;
    height: 14px;
    margin-right: 18px;
    flex: none;
  }
</style>
</head>
<body>

  <section class="card card--front">
    <svg class="card__art" viewBox="0 0 757 434" aria-hidden="true">
      <circle cx="379" cy="168" r="71" fill="none" stroke="var(--paper)" stroke-width="3"/>
    </svg>
    <div class="wordmark">GLIMORA</div>
  </section>

  <section class="card card--back">
    <svg class="card__art" viewBox="0 0 757 434" aria-hidden="true">
      <rect width="757" height="434" fill="var(--rose)"/>
      <path class="wave-body" d="M0,28 C120,4 260,24 360,72 C440,110 500,146 600,152 C680,156 720,156 757,156 L757,434 L0,434 Z" fill="var(--paper)"/>
      <path class="wave-swoosh" d="M0,14 C120,-6 260,14 360,62 C440,102 500,140 600,146 C680,150 720,142 757,138 L757,156 C720,156 680,156 600,152 C500,146 440,110 360,72 C260,24 120,4 0,28 Z" fill="var(--plum)"/>
      <path class="wave-edge" d="M0,14 C120,-6 260,14 360,62 C440,102 500,140 600,146 C680,150 720,142 757,138" fill="none" stroke="var(--paper)" stroke-width="3"/>
      <g fill="var(--paper)">
        <circle cx="530" cy="38" r="14"/>
        <circle cx="571" cy="38" r="14"/>
        <circle cx="612" cy="38" r="14"/>
        <circle cx="653" cy="38" r="14"/>
      </g>
      <circle cx="589" cy="149" r="68" fill="var(--paper)" stroke="var(--plum)" stroke-width="4"/>
    </svg>

    <div class="contact">
      <div class="contact__name">LENA VAROUX</div>
      <div class="contact__role">OWNER</div>
      <div class="contact__address">48 Palm Reed Way<br>Coral Bay, FL 33071</div>
      <ul class="contact__list">
        <li>
          <svg class="contact__icon" viewBox="0 0 14 14" aria-hidden="true"><path d="M3,2 L5,2 L6,5 L4.6,6 C5.4,7.8 6.4,8.8 8,9.4 L9,8 L12,9 L12,11 C12,11.6 11.6,12 11,12 C6.5,12 2,7.5 2,3 C2,2.4 2.4,2 3,2 Z" fill="var(--rose)"/></svg>
          555.014.2290
        </li>
        <li>
          <svg class="contact__icon" viewBox="0 0 14 14" aria-hidden="true"><rect x="1.5" y="3.5" width="11" height="7.5" rx="1" fill="none" stroke="var(--rose)" stroke-width="1.4"/><path d="M2,4 L7,8 L12,4" fill="none" stroke="var(--rose)" stroke-width="1.4"/></svg>
          info@glimora-example.com
        </li>
        <li>
          <svg class="contact__icon" viewBox="0 0 14 14" aria-hidden="true"><circle cx="7" cy="7" r="5.5" fill="none" stroke="var(--rose)" stroke-width="1.4"/><path d="M1.5,7 L12.5,7 M7,1.5 C4.5,4.5 4.5,9.5 7,12.5 M7,1.5 C9.5,4.5 9.5,9.5 7,12.5" fill="none" stroke="var(--rose)" stroke-width="1.1"/></svg>
          www.glimora-example.com
        </li>
      </ul>
    </div>

    <div class="wordmark">GLIMORA</div>
  </section>

</body>
</html>
```